Brantor Works Business Card

Modern and Professional Business Card for a Med size construction/development company.

See the samples below for the design I like … but I need ideas for incorporating the red company logo while still keeping the clean look of the card samples that are attached.

Logo and tag line on the back … info on the front.

Tagline: Solid Work from the Footing Up

Target Market(s)

Med-Large General Contractors

Contact Information for Business Card

Brantor Works Limited
42 Fenwick Avenue
Mt. Pearl, NL
A1N 4R9

t: 709-555-0147
f: 709-555-0182
w: www.brantorworks-example.com

Font styles to use
Sans Serif

Colors
fbee3e

Requirements
Must have
• I like the black and yellow designs of the attached samples …. but I'm not sure how to incorporate the red Brantor Works logo into that design??
Nice to have
• Construction safety strips

```html
<!DOCTYPE html>
<html lang="en">
<head>
<meta charset="utf-8">
<title>Brantor Works Business Card</title>
<link href="https://fonts.googleapis.com/css2?family=Questrial&family=Poppins:wght@700&display=swap" rel="stylesheet">
<style>
  :root {
    --bg: #3a3d42;
    --card: #07080b;
    --yellow: #fbee3e;
    --red: #ec1c24;
    --white: #f2f2f2;
  }
  * { box-sizing: border-box; margin: 0; padding: 0; }
  html, body { width: 1200px; height: 1000px; overflow: hidden; }
  body {
    background: var(--bg);
    font-family: "Questrial", "Century Gothic", sans-serif;
    color: var(--white);
    position: relative;
  }
  .card {
    position: absolute;
    left: 220px;
    width: 760px;
    height: 434px;
    background: var(--card);
    border-radius: 18px;
    box-shadow: 0 12px 30px rgba(0,0,0,.45);
  }
  .card-back { top: 50px; }
  .card-front { top: 516px; }

  /* Back: name and tagline */
  .brand {
    position: absolute;
    left: 0; right: 0;
    top: 150px;
    display: flex;
    justify-content: center;
    align-items: center;
    gap: 14px;
    font-size: 40px;
    line-height: 1;
    color: var(--white);
    letter-spacing: 1px;
  }
  .brand-mark {
    width: 30px;
    height: 30px;
    background: var(--red);
    border-radius: 4px;
    flex: none;
  }
  .tagline {
    position: absolute;
    left: 0; right: 0;
    top: 262px;
    text-align: center;
    font-size: 17px;
    color: var(--white);
    letter-spacing: .5px;
  }

  /* Front: details */
  .company {
    position: absolute;
    right: 440px;
    top: 148px;
    text-align: right;
    font-family: "Poppins", sans-serif;
    font-weight: 700;
    font-size: 24px;
    line-height: 1.25;
    color: var(--yellow);
  }
  .divider {
    position: absolute;
    left: 342px;
    top: 150px;
    width: 2px;
    height: 96px;
    background: var(--yellow);
  }
  .contacts {
    position: absolute;
    left: 364px;
    top: 140px;
    list-style: none;
    font-size: 17px;
    line-height: 28px;
    color: var(--white);
  }
  .contacts li { display: flex; align-items: center; gap: 10px; }
  .contacts svg { width: 15px; height: 15px; fill: var(--yellow); flex: none; }
  .contacts .accent { color: var(--yellow); }
  .address {
    position: absolute;
    left: 0; right: 0;
    top: 340px;
    text-align: center;
    font-size: 19px;
    color: var(--white);
    letter-spacing: .5px;
  }
</style>
</head>
<body>
  <section class="card card-back">
    <div class="brand"><span class="brand-mark"></span><span>Brantor Works</span></div>
    <p class="tagline">Solid Work from the Footing Up</p>
  </section>

  <section class="card card-front">
    <h1 class="company">Brantor Works<br>Limited</h1>
    <div class="divider"></div>
    <ul class="contacts">
      <li>
        <svg viewBox="0 0 16 16" aria-hidden="true"><path d="M3.5 1.5l2.5 0 1 3.5-1.6 1.2a9 9 0 0 0 4.4 4.4L11 9l3.5 1v2.5c0 1-1 2-2 2A11 11 0 0 1 1.5 3.5c0-1 1-2 2-2z"/></svg>
        <span>709-555-0147</span>
      </li>
      <li>
        <svg viewBox="0 0 16 16" aria-hidden="true"><path d="M4 1h8v4H4zM1 6h14v6h-3v3H4v-3H1zM5 10v4h6v-4z"/></svg>
        <span>709-555-0182</span>
      </li>
      <li>
        <svg viewBox="0 0 16 16" aria-hidden="true"><path d="M1 3h14v10H1zM2.5 4.5v.6L8 9l5.5-3.9v-.6L8 8.2z"/></svg>
        <span>info@brantorworks-example.com</span>
      </li>
      <li>
        <svg viewBox="0 0 16 16" aria-hidden="true"><circle cx="8" cy="8" r="7"/></svg>
        <span>www.<span class="accent">brantorworks-example</span>.com</span>
      </li>
    </ul>
    <p class="address">42 Fenwick Avenue Eastvale, NL A0A 1B2</p>
  </section>
</body>
</html>
```